Business Card Design for Marketing Firm

Looking for business card design for higher end marketing firm. Clean but impressionable/trendy. We are a marketing firm that represents manufacturers in the foodservice equipment and supply industry. Our customers are end users such has hotels, restaurants, country clubs, convention centers and casinos as well as distributors of restaurants supplies and equipment, and manufacturers of foodservice equipment and supplies.
Target Market(s)
Hotels, Restaurants, Supply & Equipment Distributors, Foodservice Manufacturers
Industry/Entity Type
Foodservice/Hospitality
Contact Information for Business Card
Name, Title, Contact Number, Email, Website, Social Media, Address
Requirements
Must have
- Clean & Simple but Serious and Impressionable

```html
<!DOCTYPE html>
<html lang="en">
<head>
<meta charset="utf-8">
<title>Meridian Hospitality Reps – Business Card</title>
<link href="https://fonts.googleapis.com/css2?family=Figtree:wght@400;600;700&display=swap" rel="stylesheet">
<style>
  :root {
    --backdrop: #e4e4e4;
    --card: #f7f7f7;
    --navy: #25266f;
    --ink: #3a3a3a;
  }
  * { margin: 0; padding: 0; box-sizing: border-box; }
  html, body {
    width: 1200px; height: 1200px; overflow: hidden;
    background: var(--backdrop);
    font-family: "Figtree", Arial, sans-serif;
  }
  .card {
    position: absolute;
    left: 234px;
    width: 730px; height: 416px;
    background: var(--card);
    box-shadow: 0 6px 18px rgba(0,0,0,0.12);
  }
  .card--front { top: 160px; }
  .card--back { top: 632px; }

  .brand-lockup {
    position: absolute;
    left: 0; right: 0; top: 96px;
    display: flex; flex-direction: column; align-items: center;
    color: var(--navy);
  }
  .brand-lockup__dot {
    width: 120px; height: 120px; border-radius: 50%;
    background: var(--navy);
  }
  .brand-lockup__name {
    margin-top: 44px;
    width: 430px;
    font-weight: 600;
    font-size: 34px;
    line-height: 40px;
    letter-spacing: 2px;
    text-transform: uppercase;
  }
  .brand-lockup__line { display: block; white-space: nowrap; }
  .brand-lockup__line--right { text-align: right; }

  .brand-mini {
    position: absolute;
    right: 60px; top: 60px;
    display: flex; align-items: center; gap: 10px;
    color: var(--navy);
    font-weight: 600;
    font-size: 18px;
    letter-spacing: 1.5px;
    text-transform: uppercase;
  }
  .brand-mini__dot {
    width: 44px; height: 44px; border-radius: 50%;
    background: var(--navy);
  }

  .person {
    position: absolute;
    right: 431px; top: 186px;
    text-align: right;
  }
  .person__name {
    color: var(--navy);
    font-weight: 700;
    font-size: 31px;
    line-height: 1;
  }
  .person__title {
    margin-top: 8px;
    color: var(--ink);
    font-size: 19px;
  }

  .contact {
    position: absolute;
    left: 334px; top: 164px;
    list-style: none;
  }
  .contact__item {
    display: flex; align-items: center; gap: 8px;
    height: 28.5px;
    color: var(--ink);
    font-size: 19px;
  }
  .contact__icon { width: 16px; height: 16px; flex: none; }

  .address {
    position: absolute;
    left: 0; right: 0; top: 338px;
    text-align: center;
    color: var(--ink);
    font-size: 19px;
  }
</style>
</head>
<body>
  <section class="card card--front">
    <div class="brand-lockup">
      <span class="brand-lockup__dot"></span>
      <div class="brand-lockup__name">
        <span class="brand-lockup__line">Meridian Hospitality</span>
        <span class="brand-lockup__line brand-lockup__line--right">Reps</span>
      </div>
    </div>
  </section>

  <section class="card card--back">
    <div class="brand-mini"><span class="brand-mini__dot"></span>Meridian</div>

    <div class="person">
      <div class="person__name">Dorian Vale</div>
      <div class="person__title">Founder &amp; Director</div>
    </div>

    <ul class="contact">
      <li class="contact__item">
        <svg class="contact__icon" viewBox="0 0 16 16"><path fill="#25266f" d="M3.5 1.5l2.5 0 1 3.5-1.6 1.2a8 8 0 0 0 4.4 4.4L11 9l3.5 1v2.5c0 .8-.7 1.5-1.5 1.5A11.5 11.5 0 0 1 2 3c0-.8.7-1.5 1.5-1.5z"/></svg>
        (555)-214-7730
      </li>
      <li class="contact__item">
        <svg class="contact__icon" viewBox="0 0 16 16"><rect x="1" y="3" width="14" height="10" rx="1.5" fill="#25266f"/><path d="M2 4.5l6 4.5 6-4.5" fill="none" stroke="#f7f7f7" stroke-width="1.4"/></svg>
        vale@meridianhospitalityreps.com
      </li>
      <li class="contact__item">
        <svg class="contact__icon" viewBox="0 0 16 16"><circle cx="8" cy="8" r="7" fill="#25266f"/><g fill="none" stroke="#f7f7f7" stroke-width="1"><ellipse cx="8" cy="8" rx="3" ry="7"/><path d="M1 8h14M2.2 4.5h11.6M2.2 11.5h11.6"/></g></svg>
        www.meridianhospitalityreps.com
      </li>
      <li class="contact__item">
        <svg class="contact__icon" viewBox="0 0 16 16"><circle cx="8" cy="8" r="7.5" fill="#25266f"/></svg>
        @meridianhospitalityreps
      </li>
    </ul>

    <p class="address">4170 Harbor Lane Westbrook Maine 04092</p>
  </section>
</body>
</html>
```